Online tuition webpage design needed

Hi,
We are starting up an online tuition website for non- English speakers wishing to take an TOVAR test.

The webpage must include a place for people to enroll online in the course.
The home page must have:
• room for a logo (coming shortly, blue in colour)
• different packages of online tuition and paywick
• tool bar showing different pages
• perhaps a video, small pictures

This is my site currently:-

www.lexavotutoring.com

as you can see, I am not very sure how to create a website … The large logo is what I would like to use, but I project has not been finalized yet. Please note, I don’t like the logo being that large!

Sites that are similar to what I am doing and like the design of are:

http://www.brindacourse.com.au/fees

https://www.quorvel9x.net/index.php

http://www.lessonmasterpercival.co.uk/index.html

http://www.tamrunexamhub.com/

One thing I need is a place for student s to enroll, and if possible, I would like to use learnix to create exercises for students.
Currently, my site is using sitecraft. My preference is to use learnix for online activities. I am not sure if I can use both.
Thanks in advance

Target Market(s)

people wising to take an TOVAR test (English proficiency test)

Industry/Entity Type

Online

Colors
3276b5
0292cd

Requirements
Must have
• a place for enrollment and admin login for students
learnix
video
voxly, friendbook, chirpnet logos
Nice to have
• a booking calender
Should not have
• too much clutter. must be clean and professional looking

```html
<!DOCTYPE html>
<html lang="en">
<head>
<meta charset="utf-8">
<title>TOVAR Online Tuition</title>
<link href="https://fonts.googleapis.com/css2?family=Oswald:wght@300;400&family=Open+Sans:ital,wght@0,400;0,600;0,700;1,400&display=swap" rel="stylesheet">
<style>
:root{
  --brand:#0292cd;
  --brand-deep:#3276b5;
  --ink:#4a4a4a;
  --muted:#666;
  --hero-band:#ece6e6;
  --pkg-bg:#ececec;
  --video-bg:#d9d9d9;
  --footer:#2e2e2e;
  --white:#fff;
}
*{box-sizing:border-box;margin:0;padding:0}
html,body{width:1192px;height:1200px;overflow:hidden}
body{font-family:"Open Sans",sans-serif;color:var(--ink);background:var(--white);position:relative}
.abs{position:absolute}

/* header */
.site-header{position:absolute;left:0;top:0;width:1192px;height:103px;border-top:3px solid var(--brand-deep);background:var(--white);box-shadow:0 2px 4px rgba(0,0,0,.12);z-index:2}
.brand{position:absolute;left:133px;top:26px;display:flex;align-items:center;gap:10px;color:var(--brand-deep);font-weight:600;font-size:22px;line-height:1}
.brand-dot{width:34px;height:34px;border-radius:50%;background:var(--brand-deep)}
.top-btn{position:absolute;top:0;height:24px;background:var(--brand);color:var(--white);font-size:13px;line-height:24px;text-align:center;border-radius:0 0 3px 3px}
.main-nav{position:absolute;left:428px;top:66px;display:flex;height:34px;font-size:12.5px;color:#777}
.main-nav a{display:block;padding:0 11px;line-height:38px;color:inherit;text-decoration:none}
.main-nav a.active{background:var(--brand);color:var(--white);border-radius:3px 3px 0 0}

/* hero */
.hero{position:absolute;left:0;top:103px;width:1192px;height:272px;background:var(--hero-band)}
.hero-frame{position:absolute;left:130px;top:13px;width:931px;height:259px;background:#f7f5f5;overflow:hidden}
.hero-photo{position:absolute;left:325px;top:0;width:606px;height:259px;background:linear-gradient(90deg,#f7f5f5 0%,#d8d2cd 25%,#b9b7c2 55%,#dfe0e6 80%,#c8b28a 100%)}
.hero-title{position:absolute;left:21px;font-family:"Oswald",sans-serif;font-weight:300;font-size:25px;color:#3a3a3a;line-height:1}
.hero-title b{font-weight:300;color:var(--brand)}
.hero-cta{position:absolute;left:21px;top:231px;width:127px;height:30px;background:var(--brand);color:var(--white);font-size:19px;line-height:32px;text-align:center}
.hero-arrow{position:absolute;top:138px;font-size:22px;color:#333;font-weight:700}

/* welcome */
.welcome-title{position:absolute;left:148px;top:396px;font-family:"Oswald",sans-serif;font-weight:400;font-size:25px;color:#3d3d3d}
.lead{position:absolute;left:148px;font-size:16px;color:var(--brand)}
.features{position:absolute;left:158px;top:492px;list-style:none;font-size:12px;color:#444}
.features li{height:20.5px;padding-left:15px;position:relative}
.features li::before{content:"";position:absolute;left:1px;top:5px;width:5px;height:5px;border-right:2px solid var(--brand);border-top:2px solid var(--brand);transform:rotate(45deg)}

/* calendar */
.calendar{position:absolute;left:837px;top:398px;width:209px;height:176px;background:#1f1f1f;border:2px solid #111;padding:4px 6px}
.cal-head{height:24px;color:var(--white);font-size:9px;font-weight:700;text-align:center;line-height:22px;position:relative}
.cal-nav{position:absolute;top:3px;width:16px;height:16px;border-radius:50%;background:#555}
.cal-grid{display:grid;grid-template-columns:repeat(7,1fr);gap:1px;background:#999}
.cal-grid span{height:19.6px;background:#ececec;font-size:8px;font-weight:700;text-align:center;line-height:19.6px;color:#222}
.cal-grid .dow{background:#d0d0d0;color:#555;font-style:italic;font-weight:400;height:14px;line-height:14px}
.cal-grid .off{color:#aaa}
.cal-grid .today{background:#4a9de0;color:var(--white)}

/* packages */
.packages{position:absolute;left:0;top:627px;width:1192px;height:310px;background:var(--pkg-bg)}
.section-title{position:absolute;font-family:"Oswald",sans-serif;font-weight:300;font-size:26px;color:#3a3a3a}
.view-all{position:absolute;left:987px;top:14px;width:58px;height:22px;background:var(--brand);color:var(--white);font-size:12px;text-align:center;line-height:22px}
.plan{position:absolute;top:62px;width:230px;text-align:center}
.plan h3{font-size:24px;font-weight:700;color:var(--brand);line-height:1.2}
.plan .price{font-size:17px;font-style:italic;color:#333;margin-top:8px}
.plan p{font-size:12px;line-height:20.5px;color:#666;margin-top:6px}
.plan .register{display:block;font-size:12px;color:var(--brand-deep);margin-top:10px}
.pay-btn{position:absolute;left:952px;top:257px;width:94px;height:31px;border-radius:5px;background:linear-gradient(#ffe7a3,#f4b73b);border:1px solid #d9a13a;color:var(--brand-deep);font-size:14px;font-weight:700;text-align:center;line-height:29px}

/* videos */
.videos{position:absolute;left:0;top:937px;width:1192px;height:213px;background:var(--video-bg)}
.video{position:absolute;top:50px;width:173px}
.video-thumb{width:173px;height:125px;background:linear-gradient(160deg,#3a5fa8,#1f2d52)}
.video-thumb.warm{background:linear-gradient(160deg,#3b2a22,#b8574a)}
.video-thumb.blue{background:linear-gradient(160deg,#3347a8,#5c6fd0)}
.video-thumb.stage{background:linear-gradient(160deg,#2f6fbf,#1a1f2b)}
.video-title{font-size:14px;color:#333;margin-top:8px}

/* footer */
.site-footer{position:absolute;left:0;top:1150px;width:1192px;height:50px;background:var(--footer);color:#ccc;font-size:12px}
.copyright{position:absolute;left:149px;top:17px}
.social{position:absolute;left:885px;top:16px;display:flex;gap:14px;font-size:11px;color:#ddd}
.social span{display:flex;align-items:center;gap:5px}
.social i{width:12px;height:12px;background:var(--brand);display:block}
</style>
</head>
<body>

<header class="site-header">
  <div class="brand"><span class="brand-dot"></span>TOVAR Online Tuition</div>
  <a class="top-btn" style="left:850px;width:90px">Enroll Now</a>
  <a class="top-btn" style="left:954px;width:107px">Student Login</a>
  <nav class="main-nav">
    <a class="active">Home</a>
    <a>Tutorial Packages</a>
    <a>Weekly Tips and Comments</a>
    <a>Reading</a>
    <a>Speaking</a>
    <a>Listening</a>
    <a>Writing</a>
  </nav>
</header>

<section class="hero">
  <span class="hero-arrow" style="left:106px">&#10094;</span>
  <div class="hero-frame">
    <div class="hero-photo" role="img" aria-label="Student working on a laptop"></div>
    <div class="hero-title" style="top:22px"><b>O</b>nline <b>T</b>OVAR <b>T</b>uition</div>
    <div class="hero-title" style="top:67px">Professional Help For People Taking</div>
    <div class="hero-title" style="top:112px">An TOVAR Test</div>
    <a class="hero-cta">Enroll Now</a>
  </div>
  <span class="hero-arrow" style="left:1073px">&#10095;</span>
</section>

<h1 class="welcome-title">Welcome To TOVAR Online Tuition</h1>
<p class="lead" style="top:432px">We put you first. We listen to you and help you find what you need.</p>
<p class="lead" style="top:459px">If you want help in passing an TOVAR test, we can help you with:</p>
<ul class="features">
  <li>Lessons in reading, writing, listening and speaking</li>
  <li>Professional teacher feedback and tips.</li>
  <li>Voxly and practice with native speakers.</li>
  <li>Quick Turnaround.</li>
  <li>Friendly and Approachable teachers.</li>
</ul>

<div class="calendar">
  <div class="cal-head"><span class="cal-nav" style="left:2px"></span>March, 2011<span class="cal-nav" style="right:2px"></span></div>
  <div class="cal-grid">
    <span class="dow">Sun</span><span class="dow">Mon</span><span class="dow">Tue</span><span class="dow">Wed</span><span class="dow">Thu</span><span class="dow">Fri</span><span class="dow">Sat</span>
    <span class="off">27</span><span class="off">28</span><span>1</span><span>2</span><span>3</span><span>4</span><span>5</span>
    <span>6</span><span>7</span><span>8</span><span>9</span><span>10</span><span>11</span><span>12</span>
    <span>13</span><span>14</span><span>15</span><span>16</span><span>17</span><span class="today">18</span><span>19</span>
    <span>20</span><span>21</span><span>22</span><span>23</span><span>24</span><span>25</span><span>26</span>
    <span>27</span><span>28</span><span>29</span><span>30</span><span>31</span><span class="off">1</span><span class="off">2</span>
    <span class="off">3</span><span class="off">4</span><span class="off">5</span><span class="off">6</span><span class="off">7</span><span class="off">8</span><span class="off">9</span>
  </div>
</div>

<section class="packages">
  <h2 class="section-title" style="left:149px;top:6px">Tutorial Packages</h2>
  <a class="view-all">View All</a>
  <div class="plan" style="left:134px"><h3>Gold</h3><div class="price">$99</div><p>Lorem ipsum dolor sit amet, consectetuer adipiscing elit, sed diam nonummy nibh euismod tincidunt ut laoreet dolore magna aliquam erat volutpat</p><a class="register">Register Now</a></div>
  <div class="plan" style="left:472px"><h3>Diamond</h3><div class="price">$79</div><p>Lorem ipsum dolor sit amet, consectetuer adipiscing elit, sed diam nonummy nibh euismod tincidunt ut laoreet dolore magna aliquam erat volutpat</p><a class="register">Register Now</a></div>
  <div class="plan" style="left:803px"><h3>Silver</h3><div class="price">$49</div><p>Lorem ipsum dolor sit amet, consectetuer adipiscing elit, sed diam nonummy nibh euismod tincidunt ut laoreet dolore magna aliquam erat volutpat</p><a class="register">Register Now</a></div>
  <a class="pay-btn">Paywick</a>
</section>

<section class="videos">
  <h2 class="section-title" style="left:149px;top:4px;font-weight:400">Video</h2>
  <div class="video" style="left:151px"><div class="video-thumb" role="img" aria-label="Video still of a presenter in a studio"></div><div class="video-title">Video Title Here</div></div>
  <div class="video" style="left:391px"><div class="video-thumb warm" role="img" aria-label="Video still of a presenter in front of bookshelves"></div><div class="video-title">Video Title Here</div></div>
  <div class="video" style="left:630px"><div class="video-thumb blue" role="img" aria-label="Video still of a speaker at a press conference"></div><div class="video-title">Video Title Here</div></div>
  <div class="video" style="left:870px"><div class="video-thumb stage" role="img" aria-label="Video still of a host on a TV set"></div><div class="video-title">Video Title Here</div></div>
</section>

<footer class="site-footer">
  <p class="copyright">Copyright © 2014 Tovar Online Tution, All Rights Reserved</p>
  <div class="social">
    <span><i></i>chirpnet</span>
    <span><i></i>friendbook</span>
    <span><i></i>voxly</span>
  </div>
</footer>

</body>
</html>
```